Letterhead and email signature block for school

We are a Remote School in the North West of Western Australia and I want to take our logo and use that to create a professional letter head and email signature block. A sample signature block is attached. For the Letterhead; The logo is also attached. I like the Orange and black combination of the logo, needs to include motto plus the following contact details;
PMB 4 BROOME WA
Phone: (08) 9170 3158
Fax: (08) 9170 3206
ABN: 41 287 519 302

The email signature block needs to have the following;
Dale Owen Wrenfield
Principal
Tern Ridge Hill RCS
Phone: (08) 9170 3158
Fax: (08) 9170 3206
Mobile: 0488 613 947
Email: Dale.Wrenfield@schoolnet-kx.org.au

Target Market(s)

Parents

Industry/Entity Type

Education

Contact Information for Business Card

Dale Owen Wrenfield
Principal
Tern Ridge Hill RCS
Phone: (08) 9170 3158
Fax: (08) 9170 3206
Mobile: 0488 613 947

Colors
f37122
000000

Requirements
Must have
• see breif

```html
<!DOCTYPE html>
<html lang="en">
<head>
<meta charset="utf-8">
<title>Tern Ridge Hill RCS – Email Signature</title>
<link rel="stylesheet" href="https://fonts.googleapis.com/css2?family=Libre+Baskerville:wght@700&family=Source+Sans+3:wght@400;600;700&display=swap">
<style>
  :root {
    --orange: #f37122;
    --orange-deep: #d8580f;
    --black: #000000;
    --ink: #1c1410;
    --rule: #2a2a2a;
    --paper: #ffffff;
  }
  html, body {
    margin: 0;
    padding: 0;
    overflow: hidden;
    background: var(--paper);
  }
  .signature {
    position: relative;
    width: 1200px;
    height: 390px;
    overflow: hidden;
    background: var(--paper);
    font-family: "Source Sans 3", Arial, sans-serif;
    color: var(--ink);
  }
  .contact {
    position: absolute;
    left: 36px;
    top: 26px;
  }
  .contact__name {
    margin: 0;
    font-family: "Libre Baskerville", Georgia, serif;
    font-weight: 700;
    font-size: 27px;
    letter-spacing: 2.5px;
    text-transform: uppercase;
    color: var(--ink);
  }
  .contact__role {
    margin: 4px 0 0;
    font-size: 23px;
    color: var(--orange);
  }
  .contact__school {
    margin: 22px 0 0;
    font-size: 31px;
    font-weight: 700;
    color: var(--ink);
  }
  .contact__line {
    margin: 8px 0 0;
    font-size: 19px;
    color: var(--ink);
  }
  .contact__label {
    font-weight: 700;
    color: var(--orange);
  }
  .contact__sep {
    margin: 0 8px;
  }
  .divider {
    position: absolute;
    left: 789px;
    top: 36px;
    width: 3px;
    height: 174px;
    background: var(--rule);
  }
  .school-mark {
    position: absolute;
    left: 840px;
    top: 34px;
    width: 300px;
    text-align: center;
  }
  .school-mark__dot {
    display: block;
    width: 96px;
    height: 96px;
    margin: 0 auto 16px;
    border-radius: 50%;
    background: var(--orange);
  }
  .school-mark__name {
    display: block;
    font-size: 30px;
    font-weight: 700;
    color: var(--ink);
  }
  .school-mark__motto {
    display: block;
    margin-top: 4px;
    font-size: 14px;
    color: var(--ink);
  }
  .waves {
    position: absolute;
    left: 0;
    bottom: 0;
    width: 1200px;
    height: 110px;
  }
</style>
</head>
<body>
  <div class="signature">
    <section class="contact">
      <h1 class="contact__name">Dale Owen Wrenfield</h1>
      <p class="contact__role">Principal</p>
      <p class="contact__school">Tern Ridge Hill RCS</p>
      <p class="contact__line">
        <span class="contact__label">Ph:</span> (08) 9170 3158<span class="contact__sep">|</span><span class="contact__label">Fax:</span> (08) 9170 3206
      </p>
      <p class="contact__line">
        <span class="contact__label">Mobile:</span> 0488 613 947<span class="contact__sep">|</span><span class="contact__label">Email:</span> Dale.Wrenfield@schoolnet-kx.org.au
      </p>
    </section>

    <div class="divider"></div>

    <div class="school-mark">
      <span class="school-mark__dot"></span>
      <span class="school-mark__name">Tern Ridge Hill RCS</span>
      <span class="school-mark__motto">Learning Together, Growing Strong, Reaching Far</span>
    </div>

    <svg class="waves" viewBox="0 0 1200 110" preserveAspectRatio="none" aria-hidden="true">
      <path d="M0 10 C 280 -6, 620 24, 1200 50 L1200 110 L0 110 Z" fill="var(--orange)"/>
      <path d="M0 24 C 300 10, 640 40, 1200 64 L1200 110 L0 110 Z" fill="var(--orange-deep)"/>
      <path d="M0 40 C 340 26, 700 58, 1200 78 L1200 110 L0 110 Z" fill="var(--black)"/>
    </svg>
  </div>
</body>
</html>
```